Summer Sunglass offer

Need a poster design for a spring / summer campaign. We are an opticians with good footfall. The design needs to be eye catching and aimed at 40 year old plus. The offer is Up to 50% off sunglass offer, t&c apply. (I have attached our last year campaign)
Also need a 2 sided A5 leaflet design (see attached)
I've uploaded a copy of our logo

A5 leaflet should read:

Grab a bargain on two great looks this summer Upto 50% off sunglasses
Look great and stay safe in the sun this summer

We want you to look great, feel fantastic and most of all stay safe in the sun this summer. That’s why we’re offering you 50% off prescription sunglasses with every complete pair of glasses you buy this summer or 25% off for prescription sunglasses with no other purchase.
Find you new summer looks from our gorgeous collection of frames in store. It matters to us that you look great in your new glasses as much as how well you see through them, so we’ll be on hand to help you find frames that suit you best.
What new looks will you go for? Smart or sassy? Formal or Fun? Whatever you’re in the mood for, you’ll find it in our collections this summer.
Call in today to find your new looks, and remember to bring your prescription if you don’t need an eye test.

Target Market(s)

40 + year old

Industry/Entity Type

Optician

Colors

Designer to choose colors to be used in the design.

Requirements
Must have
• Images, preferably a male and Female image

```html
<!DOCTYPE html>
<html lang="en">
<head>
<meta charset="utf-8">
<title>Summer Sunglasses Offer – Leaflet</title>
<link href="https://fonts.googleapis.com/css2?family=Marcellus&family=Open+Sans:wght@400;600&family=Oswald:wght@500&display=swap" rel="stylesheet">
<style>
  :root {
    --backdrop: #e4e5e6;
    --paper: #ffffff;
    --paper-soft: #f2f3f3;
    --teal: #5aafb4;
    --teal-light: #a9dbe0;
    --teal-pale: #cfeef0;
    --gold: #d4b06a;
    --ink: #4a4a4a;
    --ink-dark: #2f2f2f;
    --bar-grey: #9c9d9f;
    --white: #ffffff;
  }
  * { margin: 0; padding: 0; box-sizing: border-box; }
  html, body { width: 1200px; height: 872px; overflow: hidden; }
  body {
    background: var(--backdrop);
    position: relative;
    font-family: "Open Sans", Arial, sans-serif;
    color: var(--ink);
  }
  .leaflet {
    position: absolute;
    top: 88px;
    width: 490px;
    height: 697px;
    background: var(--paper);
    overflow: hidden;
    box-shadow: 0 6px 18px rgba(0,0,0,0.18);
  }
  .leaflet--front { left: 85px; }
  .leaflet--back { left: 625px; background: var(--paper-soft); }

  .photo { position: absolute; }
  .leaflet--front .photo {
    left: 0; top: 0; width: 490px; height: 606px;
    background: linear-gradient(90deg, #f7f7f6 0%, #ece6df 35%, #d8cbbd 60%, #b7a696 85%, #e9e3dc 100%);
  }
  .leaflet--back .photo {
    left: 60px; top: 0; width: 430px; height: 211px;
    background: linear-gradient(90deg, #e8e3dd 0%, #c9a98e 30%, #d8b9a0 55%, #9b7458 80%, #e4dcd3 100%);
  }

  .frame { position: absolute; border: 3px solid var(--white); }
  .leaflet--front .frame { left: 183px; top: 20px; width: 262px; height: 562px; }
  .leaflet--back .frame { left: 73px; top: 16px; width: 283px; height: 186px; }

  .offer-badge { position: absolute; width: 140px; height: 140px; }
  .leaflet--front .offer-badge { left: 68px; top: 208px; }
  .leaflet--back .offer-badge { left: 12px; top: 44px; width: 128px; height: 128px; }
  .offer-badge svg { position: absolute; inset: 0; width: 100%; height: 100%; }
  .offer-badge__text {
    position: absolute; inset: 0;
    display: flex; flex-direction: column; align-items: center; justify-content: center;
    font-family: "Oswald", "Arial Narrow", sans-serif;
    font-weight: 500;
    color: var(--ink-dark);
    text-transform: uppercase;
    line-height: 1.05;
    text-align: center;
  }
  .offer-badge__small { font-size: 14px; }
  .offer-badge__big { font-size: 25px; }
  .leaflet--back .offer-badge__small { font-size: 13px; }
  .leaflet--back .offer-badge__big { font-size: 23px; }

  .headline-band {
    position: absolute;
    right: 0;
    background: var(--teal);
    color: var(--white);
    text-align: center;
  }
  .leaflet--front .headline-band { left: 25px; top: 381px; height: 114px; padding-top: 14px; }
  .leaflet--back .headline-band { left: 26px; top: 216px; height: 114px; padding-top: 15px; }
  .headline {
    font-family: "Marcellus", Georgia, serif;
    font-weight: 400;
    font-size: 26px;
    line-height: 1.25;
    letter-spacing: 1.5px;
    text-transform: uppercase;
  }
  .subline { font-size: 12.5px; margin-top: 9px; }

  .body-copy {
    position: absolute;
    left: 26px; right: 22px; top: 342px;
    font-size: 11.6px;
    line-height: 1.33;
    text-align: justify;
    color: var(--ink);
  }
  .body-copy p + p { margin-top: 13px; }
  .body-copy p.tight { margin-top: 0; }

  .brand {
    position: absolute;
    left: 0; right: 0;
    text-align: center;
  }
  .leaflet--front .brand { top: 620px; }
  .leaflet--back .brand { top: 566px; }
  .brand__name {
    font-family: "Open Sans", Arial, sans-serif;
    font-weight: 600;
    font-size: 20px;
    color: var(--ink-dark);
  }

  .contact-bar {
    position: absolute;
    left: 0; right: 0; top: 621px; height: 30px;
    background: var(--bar-grey);
    color: var(--white);
    font-size: 9px;
    white-space: nowrap;
    display: flex; align-items: center; gap: 18px;
    padding-left: 24px;
  }
  .contact-bar__item { display: flex; align-items: center; gap: 6px; }
  .contact-bar svg { width: 10px; height: 10px; fill: var(--white); flex: none; }

  .web {
    position: absolute;
    left: 0; right: 0;
    display: flex; align-items: center; justify-content: center; gap: 6px;
    font-size: 11px; color: var(--ink);
  }
  .leaflet--front .web { top: 671px; }
  .leaflet--back .web { top: 668px; }
  .web svg { width: 11px; height: 11px; }
</style>
</head>
<body>

<section class="leaflet leaflet--front">
  <div class="photo" role="img" aria-label="Photo of a woman in sunglasses, white top and brown leather skirt"></div>
  <div class="frame"></div>
  <div class="offer-badge">
    <svg viewBox="0 0 140 140" aria-hidden="true">
      <circle cx="70" cy="70" r="62" fill="var(--teal-light)" opacity="0.75"/>
      <circle cx="70" cy="70" r="50" fill="var(--teal-pale)" opacity="0.7"/>
      <circle cx="72" cy="72" r="64" fill="none" stroke="var(--gold)" stroke-width="1"/>
    </svg>
    <div class="offer-badge__text">
      <span class="offer-badge__small">Upto</span>
      <span class="offer-badge__big">50% off</span>
      <span class="offer-badge__small">Sunglasses</span>
    </div>
  </div>
  <div class="headline-band">
    <h1 class="headline">Grab a bargain on two<br>great looks this summer</h1>
    <p class="subline">Look great and stay safe in the sun this summer</p>
  </div>
  <div class="brand"><span class="brand__name">Hollbrook Opticians</span></div>
  <div class="web">
    <svg viewBox="0 0 12 12" aria-hidden="true"><circle cx="6" cy="6" r="5" fill="none" stroke="#666" stroke-width="1"/><ellipse cx="6" cy="6" rx="2.2" ry="5" fill="none" stroke="#666" stroke-width="1"/><line x1="1" y1="6" x2="11" y2="6" stroke="#666" stroke-width="1"/></svg>
    <span>hollbrookopticians.co.uk</span>
  </div>
</section>

<section class="leaflet leaflet--back">
  <div class="photo" role="img" aria-label="Close-up photo of a woman wearing dark framed glasses"></div>
  <div class="frame"></div>
  <div class="offer-badge">
    <svg viewBox="0 0 140 140" aria-hidden="true">
      <circle cx="70" cy="70" r="62" fill="var(--teal-light)" opacity="0.75"/>
      <circle cx="70" cy="70" r="50" fill="var(--teal-pale)" opacity="0.7"/>
      <circle cx="72" cy="72" r="64" fill="none" stroke="var(--gold)" stroke-width="1"/>
    </svg>
    <div class="offer-badge__text">
      <span class="offer-badge__small">Upto</span>
      <span class="offer-badge__big">50% off</span>
      <span class="offer-badge__small">Sunglasses</span>
    </div>
  </div>
  <div class="headline-band">
    <h2 class="headline">Grab a bargain on two<br>great looks this summer</h2>
    <p class="subline">Look great and stay safe in the sun this summer</p>
  </div>
  <div class="body-copy">
    <p>We want you to look great, feel fantastic and most of all stay safe in the sun this summer. That’s why we’re offering you 50% off prescription sunglasses with every complete pair of glasses you buy this summer or 25% off for prescription sunglasses with no other purchase.</p>
    <p>Find you new summer looks from our gorgeous collection of frames in store. It matters to us that you love how you look in your new glasses as much as how well you see through them, so we’ll be on hand to help you find frames that suit you best.</p>
    <p>What new looks will you go for? Smart or sassy? Formal or Fun? Whatever you’re in the mood for, you’ll find it in our collections this summer.</p>
    <p class="tight">Call in today to find your new looks, and remember to bring your prescription if you don’t need an eye test.</p>
  </div>
  <div class="brand"><span class="brand__name">Hollbrook Opticians</span></div>
  <div class="contact-bar">
    <span class="contact-bar__item">
      <svg viewBox="0 0 10 10" aria-hidden="true"><path d="M5 0a3.5 3.5 0 0 0-3.5 3.5C1.5 6 5 10 5 10s3.5-4 3.5-6.5A3.5 3.5 0 0 0 5 0zm0 5a1.4 1.4 0 1 1 0-2.8A1.4 1.4 0 0 1 5 5z"/></svg>
      45 Market Street, Hollbrook, Kent HB4 2QT
    </span>
    <span class="contact-bar__item">
      <svg viewBox="0 0 10 10" aria-hidden="true"><path d="M2 0.5l1.6 2.2-1 1.1c.6 1.3 1.4 2.1 2.6 2.6l1.1-1L8.5 7 7.6 9C4 8.6 1.4 6 1 2.4z"/></svg>
      Book your appointment or call us on 01632 960418
    </span>
  </div>
  <div class="web">
    <svg viewBox="0 0 12 12" aria-hidden="true"><circle cx="6" cy="6" r="5" fill="none" stroke="#666" stroke-width="1"/><ellipse cx="6" cy="6" rx="2.2" ry="5" fill="none" stroke="#666" stroke-width="1"/><line x1="1" y1="6" x2="11" y2="6" stroke="#666" stroke-width="1"/></svg>
    <span>hollbrookopticians.co.uk</span>
  </div>
</section>

</body>
</html>
```